We are a local Communty Pharmacy wishing to promote and market a specialised Pharmaceutical Service

We would like a design that is professional and enticing ( according to the brief In attached files)
We wish to Market Compounding Pharmacy as a specialist side of our business.
We have the expertise a purpose built preparation laboratory.
The main purpose is an Internet presence that entices prospective patients to contact or visit our physical store.

Target Market(s)

Patients Medicos and Veterinary clients

Industry/Entity Type

Pharmacy

Coding

Coded - Design and coding required

Number of Pages Required

1 page

Requirements
Must have
• Clear friendly image
Nice to have
• soft enticing feel
Should not have
• No crass loud unprofessional elements

```html
<!DOCTYPE html>
<html lang="en">
<head>
<meta charset="utf-8">
<title>Brookvale Compounding Pharmacy</title>
<link href="https://fonts.googleapis.com/css2?family=Open+Sans:wght@400;600;700&family=Oswald:wght@400;500&display=swap" rel="stylesheet">
<style>
:root{
  --green:#7cbf2e;
  --green-dark:#5f9c1c;
  --blue:#1d8fd0;
  --blue-deep:#0f6fae;
  --blue-light:#dcefff;
  --ink:#4a4a4a;
  --muted:#8a8a8a;
  --orange:#f39c1a;
  --white:#ffffff;
}
*{margin:0;padding:0;box-sizing:border-box}
html,body{width:807px;height:1200px;overflow:hidden;background:var(--white)}
body{font-family:"Open Sans",Arial,sans-serif;color:var(--ink);position:relative}
.site-header{height:79px;display:flex;align-items:center;padding:0 40px;gap:30px;font-size:8px;line-height:1.45}
.brand{display:flex;align-items:center;gap:8px;width:230px}
.brand-mark{width:22px;height:22px;border-radius:50%;background:var(--blue)}
.brand-name{font-weight:700;font-size:13px;color:var(--blue-deep);line-height:1.1}
.header-address{width:220px;color:var(--muted);text-transform:uppercase}
.header-contact{margin-left:auto;color:var(--muted);text-align:left}
.main-nav{height:24px;background:var(--green);display:flex;padding-left:40px}
.main-nav a{color:var(--white);text-decoration:none;font-size:8.5px;text-transform:uppercase;padding:0 16px;line-height:24px}
.main-nav a.active{background:var(--green-dark)}
.hero{position:relative;height:205px;background:linear-gradient(120deg,#eef3f6 0%,#c9d7e0 45%,#8ea5b4 100%)}
.hero-band{position:absolute;left:0;right:0;top:93px;height:82px;background:rgba(23,128,199,.88);text-align:center;color:var(--white);font-family:"Oswald",sans-serif;padding-top:10px}
.hero-band h1{font-size:28px;font-weight:500;letter-spacing:1px}
.hero-band p{font-size:22px;font-weight:400;letter-spacing:1px}
.intro{padding:30px 60px 0;text-align:center}
.section-title{font-family:"Oswald",sans-serif;color:var(--blue);font-size:22px;font-weight:500}
.title-rule{width:80px;height:3px;background:var(--green);margin:8px auto 18px}
.intro p{font-size:8px;line-height:1.65;text-align:left;margin-bottom:10px;color:#666}
.features{position:absolute;top:620px;left:0;right:0;height:340px;background:linear-gradient(#fff, var(--blue-light))}
.features-banner{height:62px;background:var(--blue);text-align:center;color:var(--white);font-family:"Oswald",sans-serif;font-size:24px;line-height:62px}
.cards{display:flex;gap:34px;padding:22px 68px 0}
.card{width:200px}
.card-photo{height:100px;background:linear-gradient(135deg,#d8e6ee,#9fb7c6)}
.card h3{font-family:"Oswald",sans-serif;font-weight:500;font-size:12px;color:var(--blue-deep);margin:14px 0 6px;text-transform:uppercase}
.card p{font-size:7.5px;line-height:1.5;color:#666;height:40px}
.card .more{display:inline-block;background:var(--orange);color:#fff;font-size:7.5px;padding:4px 12px;margin-top:8px}
.site-footer{position:absolute;top:950px;left:0;right:0;height:250px;background:var(--blue)}
.site-footer svg.wave{position:absolute;top:-28px;left:0}
.footer-cols{display:flex;gap:40px;padding:35px 60px 0;color:var(--white);font-size:8px;line-height:1.6}
.footer-cols h4{font-family:"Oswald",sans-serif;font-weight:500;font-size:12px;margin-bottom:8px}
.footer-hours{width:160px}
.footer-address{width:250px}
.map{height:110px;background:linear-gradient(135deg,#e8efe4,#cdd9d0)}
.footer-bar{position:absolute;bottom:0;left:0;right:0;height:30px;background:var(--blue-deep);color:#cfe6f5;font-size:7.5px;line-height:30px;padding-left:60px}
</style>
</head>
<body>
<header class="site-header">
  <div class="brand"><span class="brand-mark"></span><span class="brand-name">Brookvale<br>Compounding Pharmacy</span></div>
  <div class="header-address">Brookvale Community Pharmacy<br>Unit 7, 14 Ridgeway Road<br>Brookvale 6041 West Coast</div>
  <div class="header-contact">Phone: 08 5550 1234 | Fax: 08 5550 1235<br>Email: care@brookvalepharmacy.example</div>
</header>
<nav class="main-nav">
  <a class="active" href="#">Home</a><a href="#">About Us</a><a href="#">Locations</a><a href="#">Forms</a><a href="#">Contact</a>
</nav>
<section class="hero" role="img" aria-label="Pharmacist preparing medication in a laboratory">
  <div class="hero-band">
    <h1>COMPOUNDING PHARMACY</h1>
    <p>CUSTOMISED MEDICATIONS FOR PATIENTS</p>
  </div>
</section>
<section class="intro">
  <h2 class="section-title">WHAT IS COMPOUNDING PHARMACY?</h2>
  <div class="title-rule"></div>
  <p>Compounding is the preparation of a medicine made to suit one patient. When a standard product is not the right strength, form or flavour, our pharmacists prepare a version that fits. This was once the core of every pharmacy and remains a trusted, skilled service today, guided by your doctor and our team working closely together.</p>
  <p>Our purpose built preparation laboratory lets us make creams, capsules, liquids, lozenges and more. We can remove dyes, lactose or gluten, combine several medicines into one dose, or make a dose easier to take for children and older patients. Every preparation is checked with care and made to high quality standards.</p>
  <p>We also work with vets to prepare treatments for animals, in doses and flavours that pets accept. Speak with our friendly team in store or call us to learn how compounding could help you, your patients or your animals feel better.</p>
</section>
<section class="features">
  <div class="features-banner">FEATURE ITEMS</div>
  <div class="cards">
    <article class="card">
      <div class="card-photo" role="img" aria-label="Veterinarian with a dog"></div>
      <h3>Example Vet Article</h3>
      <p>Tailored treatments for pets, made in doses and flavours that animals will take with ease, prepared with your vet.</p>
      <span class="more">READ MORE</span>
    </article>
    <article class="card">
      <div class="card-photo" role="img" aria-label="Measuring tape around a waist"></div>
      <h3>Example Slim Therapy</h3>
      <p>Support for a healthy weight with custom preparations guided by your doctor and our qualified pharmacists.</p>
      <span class="more">READ MORE</span>
    </article>
    <article class="card">
      <div class="card-photo" role="img" aria-label="Doctor examining a patient's neck"></div>
      <h3>Example Thyroid Extract</h3>
      <p>Thyroid preparations made to the exact strength you need, free from fillers that may not suit you.</p>
      <span class="more">READ MORE</span>
    </article>
  </div>
</section>
<footer class="site-footer">
  <svg class="wave" width="807" height="30" viewBox="0 0 807 30"><path d="M0 30 Q200 0 403 14 T807 8 V30 Z" fill="#1d8fd0"/></svg>
  <div class="footer-cols">
    <div class="footer-hours">
      <h4>HOURS</h4>
      Monday - Friday<br>8:30am - 6:00pm<br>Saturday<br>9:00am - 1:00pm
    </div>
    <div class="footer-address">
      <h4>OUR ADDRESS</h4>
      <div class="map" role="img" aria-label="Street map showing the pharmacy location"></div>
    </div>
    <div class="footer-contacts">
      <h4>CONTACTS</h4>
      Phone: 08 5550 1234<br>Fax: 08 5550 1235<br>care@brookvalepharmacy.example<br>Unit 7, 14 Ridgeway Road
    </div>
  </div>
  <div class="footer-bar">© Brookvale Compounding Pharmacy. All rights reserved.</div>
</footer>
</body>
</html>
```